Classy, Elegant, Simple Business Card Design

Looking to have a classy, simple, and elegant design. Want a top notch designed business card. I really like the look of the new torvane credit card. I also like the design I attached. I am trying to reach 21-29 year old females for booking us for there wedding or event. We offer Disc Jockey Service, Photo Booth Rentals, and Uplighting .

Target Market(s)

21-28 year old females

Contact Information for Business Card

Has to have logo, website, email, and phone number

Font styles to use
Other font styles liked:
• open to font choice, modern, clean
Designer to choose
33a6d7
0791cd
0555a3
ffffff

Requirements
Must have
• Has to have logo, website, email, and phone number
Nice to have
• I really like the design of the new torvane credit card. I also included my logo and some designs I like
Should not have
• clutter or too much info

```html
<!DOCTYPE html>
<html lang="en">
<head>
<meta charset="utf-8">
<title>Tidelight Event Group – Business Card</title>
<link rel="stylesheet" href="https://fonts.googleapis.com/css2?family=Poppins:wght@400;500&display=swap">
<style>
  :root {
    --backdrop: #e4e4e4;
    --card: #ffffff;
    --brand-blue: #0791cd;
    --brand-deep: #0555a3;
    --brand-light: #33a6d7;
    --text-grey: #5a5a5a;
    --muted-grey: #9a9a9a;
    --rule: #3a3a3a;
  }
  * { margin: 0; padding: 0; box-sizing: border-box; }
  html, body { width: 1200px; height: 1200px; overflow: hidden; }
  body {
    background: var(--backdrop);
    font-family: "Poppins", sans-serif;
    position: relative;
  }
  .card {
    position: absolute;
    left: 257px;
    width: 686px;
    height: 392px;
    background: var(--card);
  }
  .card--front { top: 165px; }
  .card--back { top: 653px; }

  /* front */
  .front-brand {
    position: absolute;
    left: 62px;
    top: 172px;
    width: 240px;
    text-align: center;
    font-size: 36px;
    font-weight: 500;
    color: var(--brand-blue);
    line-height: 1;
  }
  .divider {
    position: absolute;
    left: 328px;
    top: 131px;
    width: 1px;
    height: 129px;
    background: var(--rule);
  }
  .contact {
    position: absolute;
    left: 361px;
    top: 132px;
  }
  .contact__name {
    font-size: 24px;
    font-weight: 500;
    color: var(--brand-blue);
    line-height: 1.2;
    letter-spacing: 0.3px;
  }
  .contact__title {
    font-size: 16px;
    color: var(--muted-grey);
    line-height: 1.2;
    margin-bottom: 16px;
  }
  .contact__list { list-style: none; }
  .contact__item {
    display: flex;
    align-items: center;
    gap: 10px;
    font-size: 16.5px;
    color: var(--text-grey);
    line-height: 20px;
    margin-left: -5px;
  }
  .contact__item svg { width: 15px; height: 15px; flex: none; fill: var(--brand-blue); }

  /* back */
  .back-brand {
    position: absolute;
    left: 0;
    right: 0;
    top: 130px;
    display: flex;
    justify-content: center;
    align-items: center;
    gap: 14px;
    font-size: 44px;
    font-weight: 500;
    color: var(--brand-blue);
    line-height: 1;
  }
  .back-brand__dot {
    width: 18px;
    height: 18px;
    border-radius: 50%;
    background: var(--brand-blue);
  }
  .services {
    position: absolute;
    left: 0;
    right: 0;
    top: 336px;
    text-align: center;
    font-size: 16.5px;
    color: var(--text-grey);
  }
  .services__sep { color: var(--brand-blue); padding: 0 3px; }
</style>
</head>
<body>
  <section class="card card--front">
    <div class="front-brand">Tidelight</div>
    <div class="divider"></div>
    <div class="contact">
      <div class="contact__name">Daniel Reyes</div>
      <div class="contact__title">President</div>
      <ul class="contact__list">
        <li class="contact__item">
          <svg viewBox="0 0 16 16" aria-hidden="true"><path d="M1 5c0-2 3-3 7-3s7 1 7 3v1h-3V5c0-1-2-1.4-4-1.4S4 4 4 5v1H1z"/><path d="M3 7h10l1 7H2z"/><circle cx="8" cy="10.5" r="1.8" fill="#fff"/></svg>
          555-204-7731
        </li>
        <li class="contact__item">
          <svg viewBox="0 0 16 16" aria-hidden="true"><path d="M1 4h14v1L8 9.5 1 5z"/><path d="M1 6.5l7 4.5 7-4.5V13H1z"/></svg>
          info@tidelightevents.com
        </li>
        <li class="contact__item">
          <svg viewBox="0 0 16 16" aria-hidden="true"><circle cx="8" cy="8" r="7"/><path d="M4 5c2 0 3 1 2.5 3S4 9 5 12M10 3c-1 2 1 3 3 3M11 10c1 0 2 1 1 3" stroke="#fff" stroke-width="1.2" fill="none"/></svg>
          www.tidelightevents.com
        </li>
      </ul>
    </div>
  </section>

  <section class="card card--back">
    <div class="back-brand"><span class="back-brand__dot"></span>Tidelight Event Group</div>
    <p class="services">Disc Jockey Service<span class="services__sep">•</span>Photo Booth Rentals<span class="services__sep">•</span>Uplighting .</p>
  </section>
</body>
</html>
```